TalbeckLabs needs a new rocket based website

We need a new website that will be based on our rocket ship logo. We develop innovative solutions for enterprises. We would like to see a design that when the pages scroll, the rocket launches and goes from launch through a journey, similar to how we approach our customer. We would like areas for "Who are we", "What can we do", "What have we done", "How can we help". http://www.talbecklabs.example.au is our current website

Target Market(s)

Government, Enterprise, Cloud

Industry/Entity Type

Software Service

Coding

Coded - Design and coding required

Number of Pages Required

2 page

Requirements
Must have
• We would like to see a design that when the pages scroll, the rocket launches and goes from launch through a journey, similar to how we approach our customer.
• Must have a home page and a detail page.
• Would like to see the logo/rocket animate in some way when you scroll through he page.

```html
<!DOCTYPE html>
<html lang="en">
<head>
<meta charset="utf-8">
<title>TalbeckLabs</title>
<link href="https://fonts.googleapis.com/css2?family=Nunito+Sans:wght@400;600;700&family=Open+Sans:wght@400;600;700&display=swap" rel="stylesheet">
<style>
:root{
  --orange:#f28a1c;
  --orange-deep:#ea7a10;
  --ink:#2b2b2b;
  --body:#555;
  --grey-bg:#f2f2f2;
  --dark:#26282b;
  --dark-2:#2f3236;
  --white:#fff;
  --line:#d8d8d8;
}
*{box-sizing:border-box;margin:0;padding:0}
html,body{width:1200px;height:3462px;overflow:hidden}
body{font-family:"Open Sans",Arial,sans-serif;color:var(--body);background:var(--white);position:relative}
.abs{position:absolute}
h2.section-title{position:absolute;left:0;width:1200px;text-align:center;font-family:"Nunito Sans",Arial,sans-serif;font-weight:600;font-size:40px;letter-spacing:.5px;color:var(--ink)}
h2 .accent{color:var(--orange)}

/* hero */
.hero{position:absolute;left:0;top:0;width:1200px;height:670px;background:linear-gradient(160deg,#3a2418 0%,#1c1b1d 45%,#141517 100%)}
.nav-brand{position:absolute;left:113px;top:38px;display:flex;align-items:center;gap:10px;font-family:"Nunito Sans",sans-serif;font-weight:700;font-size:26px;color:var(--white)}
.nav-brand .dot{width:14px;height:14px;border-radius:50%;background:var(--orange)}
.nav{position:absolute;top:44px;left:530px;display:flex;gap:44px;list-style:none;font-size:15px;font-weight:600;color:var(--white)}
.nav .active{color:var(--orange);border-bottom:2px solid var(--orange);padding-bottom:6px}
.hero-title{position:absolute;left:110px;top:220px;font-family:"Nunito Sans",sans-serif;font-weight:600;font-size:66px;color:var(--white);letter-spacing:1px}
.hero-title span{color:var(--orange)}
.hero-lead{position:absolute;left:113px;top:322px;width:440px;font-size:12.5px;line-height:26px;color:var(--white)}
.btn-outline{position:absolute;left:113px;top:402px;width:270px;height:56px;border:2px solid var(--white);border-radius:28px;color:var(--white);font-weight:600;font-size:15px;display:flex;align-items:center;justify-content:center}
.hero-mark{position:absolute;left:560px;top:150px;width:100px;height:100px;border:3px solid var(--white);border-radius:50%}
.arrow{position:absolute;top:338px}

.notch{position:absolute;left:530px;width:140px;height:140px;border-radius:50%;display:flex;align-items:center;justify-content:center}
.notch i{width:40px;height:40px;border-radius:50%;background:var(--orange)}
.dotline{position:absolute;left:599px;border-left:3px dotted #444}

/* who */
.who-sub{position:absolute;left:200px;width:800px;top:885px;text-align:center;font-size:27px;line-height:33px;color:var(--ink)}
.who-text{position:absolute;left:360px;width:640px;text-align:center;font-size:13px;line-height:21px;color:var(--body);background:var(--white)}
.who-text p+p{margin-top:14px}

/* services */
.services{position:absolute;left:0;top:1205px;width:1200px;height:579px;background:linear-gradient(180deg,var(--orange) 0%,var(--orange-deep) 100%)}
.services h2.section-title{top:113px;color:var(--white)}
.service{position:absolute;top:230px;width:240px;text-align:center;color:var(--white)}
.service .ring{width:126px;height:126px;margin:0 auto;border-radius:50%;background:var(--white);border:6px solid rgba(255,255,255,.45);background-clip:padding-box;display:flex;align-items:center;justify-content:center}
.service h3{margin-top:22px;font-size:15px;font-weight:700;letter-spacing:.3px}
.service p{margin-top:12px;font-size:12.5px;line-height:21px;padding:0 18px}

/* done */
.done{position:absolute;left:0;top:1784px;width:1200px;height:808px;background:var(--grey-bg)}
.done h2.section-title{top:106px}
.orbit{position:absolute;left:385px;top:256px;width:430px;height:430px;border-radius:50%;border:1.5px solid #f4c89a}
.feat-icon{position:absolute;width:154px;height:154px;border-radius:50%;background:var(--grey-bg);border:2px solid #e2e2e2;display:flex;align-items:center;justify-content:center}
.center-mark{position:absolute;left:555px;top:426px;width:90px;height:90px;border-radius:50%;background:var(--orange)}
.feat{position:absolute;width:260px;font-size:13px;line-height:24px;color:var(--body)}
.feat h3{font-size:17px;font-weight:600;color:var(--ink);margin-bottom:4px}
.feat.left{text-align:right;left:97px}
.feat.right{left:845px}

/* help */
.help{position:absolute;left:0;top:2592px;width:1200px;height:870px;background:radial-gradient(circle at 80% 40%,var(--dark-2),var(--dark) 70%)}
.help h2.section-title{top:120px;color:var(--white)}
.col-title{position:absolute;font-size:24px;font-weight:600;color:var(--white);letter-spacing:.5px}
.field{position:absolute;border:1.5px solid #6b6d70;color:var(--white);font-size:14px;padding:0 18px;display:flex;align-items:center}
.field.area{align-items:flex-start;padding-top:14px}
.check{position:absolute;left:113px;top:610px;display:flex;align-items:center;gap:18px;color:var(--white);font-size:13.5px}
.check i{width:16px;height:16px;border:1.5px solid #777}
.btn-send{position:absolute;left:113px;top:661px;width:167px;height:52px;border-radius:26px;background:var(--orange);color:var(--white);font-weight:700;font-size:15px;display:flex;align-items:center;justify-content:center}
.contact-line{position:absolute;left:740px;display:flex;gap:22px;color:var(--white);font-size:19px;line-height:36px}
.contact-line .ico{width:34px;height:34px;flex:none;border-radius:50%;border:2px solid var(--orange);display:flex;align-items:center;justify-content:center;margin-top:1px}
.footer-rule{position:absolute;left:113px;top:786px;width:974px;border-top:1px solid #45484c}
.copy{position:absolute;left:113px;top:818px;font-size:11.5px;color:var(--white)}
.social{position:absolute;top:810px;width:32px;height:32px;border-radius:50%;border:1.5px solid #9a9a9a}
</style>
</head>
<body>

<header class="hero">
  <div class="nav-brand"><span class="dot"></span>TalbeckLabs</div>
  <ul class="nav">
    <li class="active">HOME</li><li>ABOUT US</li><li>SERVICES</li><li>PRICING</li><li>CONTACT US</li>
  </ul>
  <h1 class="hero-title">TALBECK<span>LABS</span></h1>
  <p class="hero-lead">Utenim inima veniam quis nostrum exercitationem ullam corporis susbo nisi utenterexeaommmm aliquid exeaommodi consequatur</p>
  <div class="btn-outline">Read More Information</div>
  <div class="hero-mark"></div>
  <svg class="arrow" style="left:36px" width="16" width="16" height="30" viewBox="0 0 16 30"><path d="M13 2 3 15l10 13" fill="none" stroke="#888" stroke-width="2"/></svg>
  <svg class="arrow" style="left:1134px" width="16" height="30" viewBox="0 0 16 30"><path d="M3 2l10 13L3 28" fill="none" stroke="#888" stroke-width="2"/></svg>
</header>

<div class="notch" style="top:595px;background:var(--white)"><i></i></div>
<div class="dotline" style="top:830px;height:375px"></div>

<h2 class="section-title" style="top:785px">WHO <span class="accent">ARE WE</span></h2>
<p class="who-sub">Excepteur sint occaecat cupidatat non proident, sunt in culpa qui officia deserunt mollit anim id est laborum</p>
<div class="who-text" style="left:360px;top:960px;width:640px;left:280px;width:640px">
  <p>Lorem ipsum dolor sit amet, consectetur adipiscing elit, sed do eiusmod tempor incididunt ut labore et dolore magna aliqua. Ut enim ad minim veniam, quis nostrud exercitation ullamco laboris nisi ut aliquip ex ea commodo consequat. Duis aute irure dolor in reprehenderit in voluptate velit esse cillum dolore eu fugiat nulla pariatur.</p>
  <p>Sed ut perspiciatis unde omnis iste natus error sit voluptatem accusantium doloremque laudantium, totam rem aperiam, eaque ipsa quae ab illo inventore veritatis et quasi architecto beatae vitae dicta sunt explicabo.</p>
</div>

<section class="services">
  <div class="dotline" style="top:0;height:90px;border-color:#333"></div>
  <h2 class="section-title">WHAT CAN WE DO</h2>
  <div class="service" style="left:95px">
    <div class="ring"><svg width="50" height="46" viewBox="0 0 50 46" fill="none" stroke="#f28a1c" stroke-width="2.5"><path d="M4 14 25 3l21 11z"/><path d="M6 14h38M10 18v18M18 18v18M32 18v18M40 18v18M4 40h42M2 44h46"/></svg></div>
    <h3>E-PARLIAMENT</h3><p>All of your Parliamentary software and business process needs.</p>
  </div>
  <div class="service" style="left:351px">
    <div class="ring"><svg width="60" height="40" viewBox="0 0 60 40" fill="none" stroke="#f28a1c" stroke-width="2.5"><path d="M14 36h34a10 10 0 0 0 0-20 14 14 0 0 0-26-4A12 12 0 0 0 14 36z"/></svg></div>
    <h3>CLOUD</h3><p>Office suites, Migration, Security, Customisations.</p>
  </div>
  <div class="service" style="left:607px">
    <div class="ring"><svg width="60" height="50" viewBox="0 0 60 50" fill="none" stroke="#f28a1c" stroke-width="2.5"><rect x="23" y="3" width="14" height="12"/><rect x="3" y="35" width="14" height="12"/><rect x="23" y="35" width="14" height="12"/><rect x="43" y="35" width="14" height="12"/><path d="M30 15v20M10 35V25h40v10"/></svg></div>
    <h3>ARCHITECTURE AND DESIGN</h3><p>Business process design, technology strategy and architecture.</p>
  </div>
  <div class="service" style="left:863px">
    <div class="ring"><svg width="56" height="50" viewBox="0 0 56 50" fill="none" stroke="#f28a1c" stroke-width="2.5"><rect x="3" y="3" width="50" height="34"/><path d="M28 37v8M16 47h24M22 14l-6 6 6 6M34 14l6 6-6 6M31 12l-6 16"/></svg></div>
    <h3>SOFTWARE DEVELOPMENT</h3><p>All of your Parliamentary software and business process needs.</p>
  </div>
</section>

<section class="done">
  <div class="dotline" style="top:0;height:80px"></div>
  <h2 class="section-title">WHAT <span class="accent">HAVE WE DONE</span></h2>
  <div class="dotline" style="top:170px;height:640px"></div>
  <div class="orbit"></div>
  <div class="center-mark"></div>

  <div class="feat-icon" style="left:360px;top:265px"><svg width="60" height="60" viewBox="0 0 60 60" fill="none" stroke="#333" stroke-width="2.2"><path d="M50 10C38 10 26 20 20 32l8 8c12-6 22-18 22-30z"/><circle cx="38" cy="22" r="4"/><path d="M20 32l-8-2 6-8h8M28 40l2 8 8-6v-8M18 42l-8 8M22 46l-6 6M14 38l-6 6"/></svg></div>
  <div class="feat-icon" style="left:676px;top:265px"><svg width="64" height="64" viewBox="0 0 64 64" fill="none" stroke="#333" stroke-width="2.2"><path d="M54 32A22 22 0 1 1 32 10M32 10l-5-4M32 10l-5 4"/><text x="16" y="37" font-family="Open Sans,sans-serif" font-size="13" font-weight="700" fill="#333" stroke="none">24</text><text x="36" y="37" font-family="Open Sans,sans-serif" font-size="13" font-weight="700" fill="#333" stroke="none">7</text></svg></div>
  <div class="feat-icon" style="left:360px;top:523px"><svg width="60" height="64" viewBox="0 0 60 64" fill="none" stroke="#333" stroke-width="2.2"><path d="M22 44c0-6-8-10-8-20a16 16 0 0 1 32 0c0 10-8 14-8 20zM23 50h14M25 56h10M30 30v14M26 30h8"/><path d="M30 2v4M8 24H4M56 24h-4M12 8l3 3M48 8l-3 3"/></svg></div>
  <div class="feat-icon" style="left:676px;top:523px"><svg width="56" height="64" viewBox="0 0 56 64" fill="none" stroke="#333" stroke-width="2.2"><path d="M30 54H6V4h36v26"/><path d="M12 14h24M12 22h24M12 30h14"/><circle cx="38" cy="42" r="9"/><path d="M33 50l-2 10 7-4 7 4-2-10"/></svg></div>

  <div class="feat left" style="top:285px"><h3>LATEST TECHNOLOGY</h3>Lorem ipsum dolor sit amet, consectetur adipiscing elit do eiusmod</div>
  <div class="feat right" style="top:285px"><h3>24/7 SERVICES</h3>Lorem ipsum dolor sit amet, consectetur adipiscing elit do eiusmod</div>
  <div class="feat left" style="top:542px"><h3>HIGHEST STANDARDS</h3>Lorem ipsum dolor sit amet, consectetur adipiscing elit do eiusmod</div>
  <div class="feat right" style="top:542px"><h3>CERTIFIED EXPERTS</h3>Lorem ipsum dolor sit amet, consectetur adipiscing elit do eiusmod</div>
</section>

<section class="help">
  <h2 class="section-title">HOW CAN WE HELP</h2>
  <div class="col-title" style="left:113px;top:243px">CONTACT US</div>
  <div class="field" style="left:113px;top:303px;width:250px;height:42px">Name</div>
  <div class="field" style="left:379px;top:303px;width:250px;height:42px">Phone No</div>
  <div class="field" style="left:113px;top:365px;width:516px;height:42px">Email</div>
  <div class="field" style="left:113px;top:426px;width:516px;height:42px">Convinient time to call You</div>
  <div class="field area" style="left:113px;top:488px;width:516px;height:96px">Message</div>
  <div class="check"><i></i>I agree to receiving terms and conditions</div>
  <div class="btn-send">Send Message</div>

  <div class="col-title" style="left:740px;top:243px">OUR ADDRESS</div>
  <div class="contact-line" style="top:300px"><span class="ico"><svg width="16" height="16" viewBox="0 0 16 16"><path d="M3 1l3 3-2 2c1 2 3 4 6 6l2-2 3 3-2 2C7 15 1 9 1 3z" fill="#f28a1c"/></svg></span>1300 555 019</div>
  <div class="contact-line" style="top:365px"><span class="ico"><svg width="16" height="12" viewBox="0 0 16 12"><rect x="1" y="1" width="14" height="10" fill="#f28a1c"/><path d="M1 1l7 6 7-6" fill="none" stroke="#26282b" stroke-width="1.3"/></svg></span>info@talbecklabs.example.au</div>
  <div class="contact-line" style="top:433px"><span class="ico"><svg width="12" height="16" viewBox="0 0 12 16"><path d="M6 15C2 10 1 8 1 6a5 5 0 0 1 10 0c0 2-1 4-5 9z" fill="#f28a1c"/><circle cx="6" cy="6" r="2" fill="#26282b"/></svg></span><span>Unit 8, 41 Fenwick St<br>Norwood, SA 5067</span></div>

  <div class="footer-rule"></div>
  <div class="copy">© copyright 2018 &nbsp;TalbeckLabs.All Rights Reserved &nbsp;| &nbsp;Privacy policy</div>
  <div class="social" style="left:976px"></div>
  <div class="social" style="left:1015px"></div>
  <div class="social" style="left:1054px"></div>
</section>

<div class="notch" style="top:2522px;background:var(--grey-bg)"><i></i></div>

</body>
</html>
```